Martial Arts Website

Redevelopment of existing martial arts website.

The academy teaches traditional shaolin martial arts, including Shaolin Kung Fu, Wu Shu, Tai Chi, Qigong and Wing Chun and the site needs to reflect the traditional roots (eg, no tacky boxing imagery)

Existing website is www.copperlantern.com.au to get a feel for the desired color scheme (black, green and red). The exact colors can be tweaked though. Please only reuse the logo and font (Karate) - there isnt anything else from the current design that needs to remain.

The current website includes links to a ClipHarbor channel that includes demonstrations of the training conducted to better guide the design.

The new website site map will be:
1. Home
2. Programs - summary page describing each form of training
a. Tiny Otters
b. Kids Kung Fu
c. Youth Kung Fu
d. Adults Kung Fu
e. Wing Chun
f. Tai Chi & Qigong
g. Weaponry Classes
h. 72 Arts of Shaolin Conditioning Program
i. Acrobatics and Wu Shu
j. Fitness Boxing
3. Timetable
4. Coaches - summary page describing all coaches
a. Sifu (Master)
b. Sihing Kit
c. Sihing Sam
d. Sihing Marcus
X. ... up to 10 or so coaches
5. Member Zone
6. Contact Us
Updates

Logo now attached to brief - sorry I only have it in PDF

Just to clarify, I am only expecting a PSD design - no HTML required

Reason: Thanks for the designs, we love a lot of them just require a little extra time to tweak the designs and establish the potential. Thanks for your understanding and efforts.

Target Market(s)

Parents, teenagers, young adults, adults, elderly

Industry/Entity Type

Training

Requirements
Must have
• Chinese kung fu dragon imagery throughout the background
Links to Chatterly and ClipHarbor channel
Promo/icon in the header "Try 2 free classes now"
Home page should include an embedded ClipHarbor video

```html
<!DOCTYPE html>
<html lang="en">
<head>
<meta charset="utf-8">
<title>Contact &amp; Location – Copper Lantern Martial Arts Academy</title>
<link href="https://fonts.googleapis.com/css2?family=Arimo:ital,wght@0,400;0,700;1,400;1,700&family=Cinzel:wght@700&display=swap" rel="stylesheet">
<style>
:root{
  --black:#000;
  --green:#1f6f16;
  --green-dark:#11420c;
  --green-light:#3f9a2e;
  --red:#a50d0d;
  --red-bright:#c01414;
  --grey-panel:#8a8a8a;
  --grey-panel-dark:#5e5e5e;
  --text:#111;
  --muted:#444;
  --line:#777;
  --input-bg:#f4f4f4;
}
*{box-sizing:border-box;margin:0;padding:0}
html,body{width:1145px;height:1200px;overflow:hidden}
body{position:relative;background:var(--black);font-family:"Arimo",Arial,sans-serif;color:var(--text)}

.backdrop{position:absolute;top:285px;width:170px;height:915px;background:linear-gradient(180deg,#1d1d1d,#0c0c0c 50%,#1a1a1a)}
.backdrop.left{left:0}
.backdrop.right{left:973px;width:172px;background:linear-gradient(180deg,#0a0a0a,#1c1c1c 60%,#111)}

.site-header{position:absolute;left:0;top:0;width:1145px;height:189px;background:var(--black);text-align:center}
.brand-name{position:absolute;left:0;right:0;top:74px;font-family:"Cinzel",serif;font-weight:700;font-size:50px;letter-spacing:3px;color:var(--green)}
.brand-sub{position:absolute;left:0;right:0;top:136px;font-family:"Cinzel",serif;font-weight:700;font-size:17px;letter-spacing:4px;color:var(--red-bright)}
.brand-tag{position:absolute;left:0;right:0;top:158px;font-size:10px;letter-spacing:2.4px;color:#fff}

.main-nav{position:absolute;left:0;top:189px;width:1145px;height:38px;background:#fff}
.main-nav a{position:absolute;top:10px;font-size:12.5px;color:#333;text-decoration:none;transform:translateX(-50%)}
.main-nav .sep{position:absolute;top:6px;width:1px;height:24px;background:#ccc}
.main-nav .current{position:absolute;left:786px;top:-14px;width:91px;height:41px;background:var(--red);color:#fff;font-size:12.5px;padding-top:24px;text-align:center}

.title-band{position:absolute;left:0;top:227px;width:1145px;height:58px;background:linear-gradient(180deg,var(--green-light),var(--green) 55%,var(--green-dark))}
.title-band h1{position:absolute;left:0;width:1145px;top:13px;text-align:center;font-family:"Cinzel",serif;font-size:27px;color:#fff;letter-spacing:1px}

.content{position:absolute;left:170px;top:285px;width:803px;height:915px;background:#fff}

.breadcrumb{position:absolute;left:237px;top:299px;font-size:12.5px;color:#555}
.lets-talk{position:absolute;left:236px;top:355px;font-family:"Cinzel",serif;font-size:19px;color:var(--green)}
.intro{position:absolute;left:236px;top:381px;font-size:14.5px;font-style:italic;font-weight:700}

.section-title{position:absolute;font-size:19.5px;font-style:italic;font-weight:700;color:var(--green)}
.note{position:absolute;left:235px;top:458px;font-size:9.5px;text-decoration:underline;color:#333;letter-spacing:.3px}

.field-label{position:absolute;left:235px;font-size:13.5px;font-weight:700}
.field{position:absolute;left:235px;width:299px;height:19px;border:1px solid var(--line);background:var(--input-bg)}

.opt{position:absolute;font-size:13.5px;color:#222}
.opt.right{right:769px;text-align:right}
.box{position:absolute;width:10px;height:10px;border:1px solid #888;border-radius:2px;background:#fff}

.comments-label{position:absolute;left:235px;top:1083px;font-size:13.5px}
.comments{position:absolute;left:235px;top:1102px;width:299px;height:37px;border:1px solid var(--line);background:var(--input-bg)}
.btn{position:absolute;top:1152px;height:22px;color:#fff;font-size:12.5px;font-weight:700;text-align:center;line-height:22px}
.btn.submit{left:236px;width:157px;background:linear-gradient(180deg,#4f8f30,#285d14)}
.btn.clear{left:407px;width:126px;background:var(--red)}

.divider{position:absolute;left:572px;top:423px;height:750px;border-left:1px dotted #888}

.info-label{position:absolute;left:612px;font-size:13.5px;font-weight:700}
.info{position:absolute;left:612px;font-size:12px;line-height:16px}

.map{position:absolute;left:585px;top:675px;width:376px;height:416px;border:1px solid #555;background:linear-gradient(135deg,#eeeeec,#e4e4e0)}
.map-links{position:absolute;left:612px;font-size:13.5px;color:#222}

.class-panel{position:absolute;left:922px;top:227px;width:209px;height:429px;background:linear-gradient(180deg,var(--grey-panel),var(--grey-panel-dark))}
.class-panel h2{position:absolute;left:22px;width:165px;top:12px;text-align:center;font-family:"Cinzel",serif;font-size:18px;color:#fff;padding-bottom:6px;border-bottom:1px dotted #ccc}
.class-item{position:absolute;left:25px;color:#fff}
.class-item svg{position:absolute;left:0;top:0}
.class-item .name{position:absolute;left:26px;top:-1px;white-space:nowrap;font-size:12.5px;font-style:italic;font-weight:700}
.class-item .age{position:absolute;left:26px;top:13px;white-space:nowrap;font-size:10px;font-style:italic}
.try-free{position:absolute;left:0;top:397px;width:209px;height:32px;background:linear-gradient(180deg,#4e9a2c,#2d6a15);color:#fff;font-size:13px;font-weight:700;line-height:32px;padding-left:11px;white-space:nowrap}
.try-free svg{position:absolute;right:7px;top:9px}
</style>
</head>
<body>

<div class="backdrop left" role="img" aria-label="Dark background of faint Chinese calligraphy columns"></div>
<div class="backdrop right" role="img" aria-label="Dark background of faint Chinese calligraphy columns"></div>

<header class="site-header">
  <div class="brand-name">COPPER LANTERN</div>
  <div class="brand-sub">MARTIAL ARTS ACADEMY</div>
  <div class="brand-tag">TRADITIONAL KUNG FU &amp; TAI CHI TRAINING CENTRE</div>
</header>

<nav class="main-nav">
  <a style="left:314px">HOME</a>
  <span class="sep" style="left:358px"></span>
  <a style="left:410px">PROGRAMS</a>
  <span class="sep" style="left:460px"></span>
  <a style="left:508px">TIMETABLE</a>
  <span class="sep" style="left:557px"></span>
  <a style="left:607px">COACHES</a>
  <span class="sep" style="left:655px"></span>
  <a style="left:715px">MEMBER ZONE</a>
  <span class="current">CONTACT US</span>
</nav>

<div class="title-band"><h1>Contact &amp; Location</h1></div>

<main class="content"></main>

<div class="breadcrumb">Home &nbsp;&nbsp;&gt;&nbsp;&nbsp; Contact Us</div>
<div class="lets-talk">Lets Talk</div>
<p class="intro">Please use this enquiry form to have one of our friendly staff answer your questions.</p>

<h2 class="section-title" style="left:234px;top:434px">Contact Information</h2>
<div class="note">Fields marked with * are required</div>

<div class="field-label" style="top:502px">First Name *</div><div class="field" style="top:520px"></div>
<div class="field-label" style="top:552px">Surname</div><div class="field" style="top:570px"></div>
<div class="field-label" style="top:603px">Phone *</div><div class="field" style="top:621px"></div>
<div class="field-label" style="top:652px">Mobile</div><div class="field" style="top:671px"></div>
<div class="field-label" style="top:702px">Email *</div><div class="field" style="top:720px"></div>
<div class="field-label" style="top:752px">Age of Student</div><div class="field" style="top:771px"></div>

<h2 class="section-title" style="left:234px;top:836px">I would like more information for:</h2>

<div class="opt right" style="top:872px">Tiny Otters</div><span class="box" style="left:393px;top:876px"></span>
<div class="opt right" style="top:893px">Kids Kung Fu (Shaolin)</div><span class="box" style="left:393px;top:897px"></span>
<div class="opt right" style="top:914px">Youth Kung Fu (Shaolin)</div><span class="box" style="left:393px;top:918px"></span>
<div class="opt right" style="top:935px">Adults Kung Fu (Shaolin)</div><span class="box" style="left:393px;top:939px"></span>
<div class="opt right" style="top:956px">Wing Chun Kung Fu</div><span class="box" style="left:393px;top:960px"></span>
<div class="opt right" style="top:978px">Tai Chi &amp; Qigong</div><span class="box" style="left:393px;top:982px"></span>
<div class="opt right" style="top:1000px">Location</div>
<div class="opt" style="left:392px;top:1000px">Kingsford</div><span class="box" style="left:471px;top:1004px"></span>
<div class="opt" style="left:392px;top:1021px">Brookvale</div><span class="box" style="left:471px;top:1025px"></span>
<div class="opt" style="left:392px;top:1043px">Harwick</div><span class="box" style="left:471px;top:1047px"></span>

<div class="comments-label">Comments</div>
<div class="comments"></div>
<div class="btn submit">SUBMIT</div>
<div class="btn clear">CLEAR</div>

<div class="divider"></div>

<h2 class="section-title" style="left:616px;top:434px">Training Centre Location</h2>
<div class="info-label" style="top:502px">Address:</div>
<div class="info" style="top:519px">Unit 7, 22 Harbour Lane,<br>Kingsford East NSW 2760</div>
<div class="info-label" style="top:567px">Phone:</div>
<div class="info" style="top:585px">(02) 5550 1842</div>
<div class="info-label" style="top:621px">Email:</div>
<div class="info" style="top:639px">kwoon@copperlantern.com.au</div>

<div class="map" role="img" aria-label="Street map showing the training centre location"></div>

<div class="map-links" style="top:1141px">View Larger Map &gt;</div>
<div class="map-links" style="top:1162px">Driving Directions &gt;</div>

<aside class="class-panel">
  <h2>ALL CLASSES</h2>
  <div class="class-item" style="top:53px"><svg width="17" height="17" viewBox="0 0 17 17"><circle cx="8.5" cy="8.5" r="8" fill="#b31212"/><path d="M4 7.5h5V5l4 3.5-4 3.5V9.5H4z" fill="#fff"/></svg><span class="name">Tiny Otters</span><span class="age">Ages 4 - 6</span></div>
  <div class="class-item" style="top:89px"><svg width="17" height="17" viewBox="0 0 17 17"><circle cx="8.5" cy="8.5" r="8" fill="#b31212"/><path d="M4 7.5h5V5l4 3.5-4 3.5V9.5H4z" fill="#fff"/></svg><span class="name">Kids Kung Fu</span><span class="age">Ages 6 - 11</span></div>
  <div class="class-item" style="top:125px"><svg width="17" height="17" viewBox="0 0 17 17"><circle cx="8.5" cy="8.5" r="8" fill="#b31212"/><path d="M4 7.5h5V5l4 3.5-4 3.5V9.5H4z" fill="#fff"/></svg><span class="name">Youth Kung Fu</span><span class="age">Ages 11 - 15</span></div>
  <div class="class-item" style="top:160px"><svg width="17" height="17" viewBox="0 0 17 17"><circle cx="8.5" cy="8.5" r="8" fill="#b31212"/><path d="M4 7.5h5V5l4 3.5-4 3.5V9.5H4z" fill="#fff"/></svg><span class="name">Adults Kung Fu</span><span class="age">Ages 15 &amp; over</span></div>
  <div class="class-item" style="top:197px"><svg width="17" height="17" viewBox="0 0 17 17"><circle cx="8.5" cy="8.5" r="8" fill="#b31212"/><path d="M4 7.5h5V5l4 3.5-4 3.5V9.5H4z" fill="#fff"/></svg><span class="name">Wing Chun</span><span class="age">Ages 13 &amp; over</span></div>
  <div class="class-item" style="top:233px"><svg width="17" height="17" viewBox="0 0 17 17"><circle cx="8.5" cy="8.5" r="8" fill="#b31212"/><path d="M4 7.5h5V5l4 3.5-4 3.5V9.5H4z" fill="#fff"/></svg><span class="name">Tai Chi &amp; Qigong</span><span class="age">All ages</span></div>
  <div class="class-item" style="top:268px"><svg width="17" height="17" viewBox="0 0 17 17"><circle cx="8.5" cy="8.5" r="8" fill="#b31212"/><path d="M4 7.5h5V5l4 3.5-4 3.5V9.5H4z" fill="#fff"/></svg><span class="name">Weaponry Classes</span><span class="age">Ages 5 and over</span></div>
  <div class="class-item" style="top:305px"><svg width="17" height="17" viewBox="0 0 17 17"><circle cx="8.5" cy="8.5" r="8" fill="#b31212"/><path d="M4 7.5h5V5l4 3.5-4 3.5V9.5H4z" fill="#fff"/></svg><span class="name">72 Arts of Shaolin</span><span class="age">Conditioning Program</span></div>
  <div class="class-item" style="top:341px"><svg width="17" height="17" viewBox="0 0 17 17"><circle cx="8.5" cy="8.5" r="8" fill="#b31212"/><path d="M4 7.5h5V5l4 3.5-4 3.5V9.5H4z" fill="#fff"/></svg><span class="name">Acrobatics and Wu Shu</span><span class="age">Performance Team</span></div>
  <div class="class-item" style="top:374px"><svg width="17" height="17" viewBox="0 0 17 17"><circle cx="8.5" cy="8.5" r="8" fill="#b31212"/><path d="M4 7.5h5V5l4 3.5-4 3.5V9.5H4z" fill="#fff"/></svg><span class="name">Fitness Boxing</span></div>
  <div class="try-free">TRY 2 FREE CLASSES NOW!<svg width="9" height="14" viewBox="0 0 9 14"><path d="M0 0l9 7-9 7z" fill="#fff"/></svg></div>
</aside>

</body>
</html>
```